Healthy Meal Delivery Website Needs to be updated, current, fresh and modern

Hi there,

The current website i have is super old and outdated.

I would like a beautiful modern site that has all the same content as the previous except with a a new, modern and trustworthy feel.

The current website is https://tovalplatefresh.com/

Target Market(s)

Health Conscious Young Professionals

Industry/Entity Type

Food Service

Font styles to use
Sans Serif

Requirements
Must have
• Modern Trustworthy feel
Should not have
• Anything out dated or cheesy or scammy

```html
<!DOCTYPE html>
<html lang="en">
<head>
<meta charset="utf-8">
<title>Toval Plate Fresh – Diet Meals Delivered</title>
<link href="https://fonts.googleapis.com/css2?family=Lato:wght@400;700;900&family=Open+Sans:ital,wght@0,400;0,600;0,700;1,400&display=swap" rel="stylesheet">
<style>
:root{
  --blue:#1a8fd6;
  --blue-dark:#1572b0;
  --yellow:#e3dc13;
  --lime:#d6d100;
  --ink:#1c1c1c;
  --text:#555;
  --muted:#777;
  --line:#dfe3e7;
  --footer:#161616;
  --white:#fff;
}
*{box-sizing:border-box;margin:0;padding:0}
html,body{width:1200px;height:3922px;overflow:hidden}
body{position:relative;background:var(--white);font-family:"Open Sans",Arial,sans-serif;color:var(--text)}
.abs{position:absolute}
h1,h2,h3,h4{font-family:"Lato",Arial,sans-serif;color:var(--ink)}

/* header */
.site-header{left:0;top:0;width:1200px;height:100px;background:var(--white)}
.brand{left:97px;top:33px;display:flex;align-items:center;gap:12px}
.brand-mark{width:30px;height:30px;background:var(--lime);border-radius:50%}
.brand-name{font-family:"Lato",sans-serif;font-weight:700;font-size:22px;color:var(--blue)}
.main-nav{right:98px;top:52px;display:flex;gap:24px;font-family:"Lato",sans-serif;font-weight:700;font-size:14px;color:var(--ink)}
.main-nav .active{color:var(--blue);position:relative}
.main-nav .active::before{content:"";position:absolute;left:11px;top:-17px;width:16px;height:8px;border-radius:0 0 10px 10px;background:var(--blue)}

/* hero */
.hero{left:0;top:100px;width:1200px;height:570px;background:linear-gradient(90deg,#f1efec 0%,#e4ddd6 28%,#d7d7d2 48%,#a9c596 68%,#7fae5c 85%,#6c9c4a 100%)}
.hero-box{left:583px;top:150px;width:516px;height:292px;background:var(--blue);padding:36px 48px}
.hero-box h1{color:var(--white);font-size:44px;line-height:1.22;font-weight:900}
.btn-yellow{display:inline-block;margin-top:30px;background:var(--yellow);color:var(--blue-dark);font-family:"Lato",sans-serif;font-weight:700;font-size:15px;padding:14px 24px;border-radius:4px}

/* intro */
.intro-title{left:0;top:762px;width:1200px;text-align:center;font-size:33px;line-height:1.6;font-weight:900}
.intro-text{left:0;top:890px;width:1200px;text-align:center;font-size:12.5px;line-height:1.75}

/* plans */
.plan-photo{border:2px solid var(--line);border-radius:3px}
.plan h3{font-size:26px;font-weight:900}
.plan p{font-size:12.5px;line-height:1.95}
.btn-outline{display:inline-flex;align-items:center;gap:6px;border:1.5px solid var(--line);border-radius:6px;color:var(--blue);font-family:"Lato",sans-serif;font-weight:700;font-size:14px;padding:0 24px;height:46px}
.arrow-dot{width:14px;height:14px;border-radius:50%;background:currentColor;display:inline-flex;align-items:center;justify-content:center}
.arrow-dot svg{display:block}

/* reasons */
.reasons{left:0;top:2049px;width:1200px;height:555px;background:linear-gradient(135deg,#1a8fd6 0%,#1e9be0 50%,#157ec4 100%);overflow:hidden}
.reasons-photo{left:0;top:0;width:560px;height:555px;background:linear-gradient(90deg,#1470ad 0%,#1b8ad0 22%,#7eaed0 40%,#c9d4dc 55%,#5aa4d8 78%,rgba(26,143,214,0) 100%)}
.reasons-edge{left:1040px;top:0;width:160px;height:555px;background:linear-gradient(90deg,rgba(21,126,196,0),#17568a)}
.reasons h2{left:601px;top:56px;font-size:34px;color:var(--white);font-weight:900}
.reason-list{left:601px;top:122px;width:500px;list-style:none;color:var(--white)}
.reason-list li{display:flex;gap:14px;margin-bottom:13px}
.reason-list .tick{flex:0 0 16px;height:16px;margin-top:2px}
.reason-list h4{color:var(--white);font-size:11.5px;font-weight:700;font-family:"Open Sans",sans-serif}
.reason-list p{font-size:12px;line-height:1.6}

/* recipes */
.recipes-title{left:0;top:2697px;width:1200px;text-align:center;font-size:32px;font-weight:700}
.recipes-sub{left:0;top:2750px;width:1200px;text-align:center;font-size:15px;color:var(--muted)}
.recipe-card{top:2815px;width:314px;height:272px;border:1.5px solid var(--line);border-radius:4px;background:var(--white);box-shadow:0 3px 8px rgba(0,0,0,.08)}
.recipe-card .photo{margin:10px;height:190px}
.recipe-card h3{text-align:center;font-family:"Open Sans",sans-serif;font-weight:600;font-size:15px;margin-top:26px}
.btn-blue{left:489px;top:3137px;width:219px;height:46px;background:var(--blue);color:var(--white);border-radius:4px;display:flex;align-items:center;justify-content:center;gap:6px;font-family:"Lato",sans-serif;font-weight:700;font-size:13px}

/* testimonial */
.testimonial{left:0;top:3283px;width:1200px;height:256px;background:radial-gradient(ellipse at 50% 50%,#ece71c,#d8d105 70%,#cbc400)}
.quote-bubble{left:100px;top:92px;width:96px;height:96px;border-radius:50%;background:var(--blue)}
.quote-photo{left:168px;top:40px;width:150px;height:150px;border-radius:50%;background:linear-gradient(135deg,#f1ede6,#cfc3b4);border:5px solid var(--white)}
.testimonial blockquote{left:366px;top:40px;width:740px;font-style:italic;font-size:15px;line-height:1.95;color:var(--ink)}
.stars{left:366px;top:150px;display:flex;gap:4px}
.cite{left:366px;top:178px;font-size:13px;color:var(--ink)}
.cite b{font-family:"Lato",sans-serif;font-size:15px}
.slider-arrow{top:112px;color:var(--ink);font-size:24px;font-weight:700}

/* footer */
.site-footer{left:0;top:3539px;width:1200px;height:383px;background:var(--footer);color:#ddd}
.site-footer h4{color:var(--white);font-size:16px;font-weight:700;font-family:"Open Sans",sans-serif}
.footer-about{left:97px;top:60px;width:290px}
.footer-about p{margin-top:28px;font-size:13.5px;line-height:1.7}
.footer-links{list-style:none;margin-top:30px;font-size:12.5px;line-height:2.15}
.footer-links li::before{content:"›";margin-right:10px}
.socials{display:flex;gap:14px;margin-top:32px}
.socials span{width:42px;height:42px;border:1.5px solid var(--white);border-radius:50%}
.footer-rule{left:97px;top:293px;width:1003px;height:1px;background:#3a3a3a}
.copyright{left:0;top:330px;width:1200px;text-align:center;font-size:12.5px}
</style>
</head>
<body>

<header class="site-header abs">
  <div class="brand abs"><span class="brand-mark"></span><span class="brand-name">Toval Plate Fresh</span></div>
  <nav class="main-nav abs">
    <span class="active">HOME</span><span>PLANS</span><span>MENU</span><span>PRICING</span><span>ABOUT</span><span>PRESS</span><span>CONTACT</span><span>LOGIN</span><span>SIGN UP</span>
  </nav>
</header>

<section class="hero abs" role="img" aria-label="Smiling woman in workout clothes eating a salad in a bright kitchen with a garden view">
  <div class="hero-box abs">
    <h1>FRESH &amp; NATURAL INGREDIENTS.</h1>
    <span class="btn-yellow">START YOUR JOURNEY ➔</span>
  </div>
</section>

<h2 class="intro-title abs">THE TOVAL DIET DELIVERS DIET MEALS<br>TO YOUR DOOR</h2>
<p class="intro-text abs">Our fresh and delicious diet meals and snacks are made with only the best natural ingredients that nourish your body.<br>Why not let us prepare your meals while you lose the weight?</p>

<div class="plan-photo abs" style="left:97px;top:988px;width:462px;height:277px;background:linear-gradient(135deg,#f4f5f1 0%,#9bb36a 35%,#5d7a34 55%,#8c4a32 75%,#eef0ea 100%)" role="img" aria-label="Steak salad with greens and tomatoes"></div>
<div class="plan abs" style="left:609px;top:986px;width:491px">
  <h3>TOVAL DIET</h3>
  <p style="margin-top:30px">The Toval Diet is based on real foods made with fresh and natural ingredients. It's about eating the foods you love and emphasizing the ones that nourish your body; generous portions of fresh fruit, vegetables, meat, fish, nuts and seeds, with smaller servings of grains and dairy. Within just a couple days of eating the gourmet meals served to you on the Toval Diet™ you'll notice a difference.</p>
  <span class="btn-outline" style="margin-top:34px">READ MORE <span class="arrow-dot"><svg width="8" height="8" viewBox="0 0 8 8"><path d="M2 1l3 3-3 3" stroke="#fff" stroke-width="1.6" fill="none"/></svg></span></span>
</div>

<div class="plan abs" style="left:97px;top:1334px;width:500px">
  <h3>TOVAL VEGGIE</h3>
  <p style="margin-top:34px">Toval Veggie™ is the vegetarian program that gives you a simple approach to losing weight while maintaining a vegetarian lifestyle. You'll receive 3 fresh daily meals and 3 fresh daily snacks delivered to your doorstep before 6am. Toval Veggie™ includes more than 100 delicious vegetarian entrees, snacks and desserts that you may select online. *Please note that this plan includes fish and dairy products.</p>
  <span class="btn-outline" style="margin-top:34px">READ MORE <span class="arrow-dot"><svg width="8" height="8" viewBox="0 0 8 8"><path d="M2 1l3 3-3 3" stroke="#fff" stroke-width="1.6" fill="none"/></svg></span></span>
</div>
<div class="plan-photo abs" style="left:643px;top:1336px;width:457px;height:266px;background:linear-gradient(135deg,#6b3a24 0%,#7fa24a 30%,#d9b88a 50%,#c8452e 70%,#4a2a1c 100%)" role="img" aria-label="Bowl with grilled chicken, avocado, quinoa and tomatoes on a wooden table"></div>

<div class="plan-photo abs" style="left:97px;top:1676px;width:462px;height:198px;background:linear-gradient(135deg,#f4f1ea 0%,#e2c27a 30%,#a8642e 50%,#c23a2a 68%,#f1efe8 100%)" role="img" aria-label="Plated patty topped with grated cheese beside tomatoes"></div>
<div class="plan abs" style="left:609px;top:1674px;width:491px">
  <h3>THE TOVAL A LA CARTE DIET</h3>
  <p style="margin-top:30px">To help you stay on track with your health and weight loss goals Toval offers you a choice of two meals a day. Receiving two meals from Toval is convenient for those who require a more flexible meal schedule and for those who want to start incorporating their own food into the Toval program. You can choose to sign up for Toval Diet or Toval Veggie, Phase 1 or 2 and choose regular or large sized meals.</p>
  <span class="btn-outline" style="margin-top:42px">READ MORE <span class="arrow-dot"><svg width="8" height="8" viewBox="0 0 8 8"><path d="M2 1l3 3-3 3" stroke="#fff" stroke-width="1.6" fill="none"/></svg></span></span>
</div>

<section class="reasons abs">
  <div class="reasons-photo abs" role="img" aria-label="Smiling woman in sportswear holding an apple, with dark cherries in the background"></div>
  <div class="reasons-edge abs" role="img" aria-label="Dark cherries"></div>
  <h2 class="abs">5 REASON TO JOIN TOVAL DIET</h2>
  <ul class="reason-list abs">
    <li><svg class="tick" viewBox="0 0 16 16"><circle cx="8" cy="8" r="8" fill="#fff"/><path d="M4.5 8.2l2.3 2.3 4.7-4.8" stroke="#1a8fd6" stroke-width="1.8" fill="none"/></svg><div><h4>WHAT YOU GET</h4><p>Toval Diet Delivery provides you with 3 fresh daily meals and 3 snacks delivered to your doorstep before 6am.</p></div></li>
    <li><svg class="tick" viewBox="0 0 16 16"><circle cx="8" cy="8" r="8" fill="#fff"/><path d="M4.5 8.2l2.3 2.3 4.7-4.8" stroke="#1a8fd6" stroke-width="1.8" fill="none"/></svg><div><h4>SELECTION</h4><p>Choose your meals from over 100 delicious entrees, snacks and desserts.</p></div></li>
    <li><svg class="tick" viewBox="0 0 16 16"><circle cx="8" cy="8" r="8" fill="#fff"/><path d="M4.5 8.2l2.3 2.3 4.7-4.8" stroke="#1a8fd6" stroke-width="1.8" fill="none"/></svg><div><h4>LUXURY</h4><p>Enjoy the luxury of having your own personal chef and nutritionist prepare Toval Diet meals for you.</p></div></li>
    <li><svg class="tick" viewBox="0 0 16 16"><circle cx="8" cy="8" r="8" fill="#fff"/><path d="M4.5 8.2l2.3 2.3 4.7-4.8" stroke="#1a8fd6" stroke-width="1.8" fill="none"/></svg><div><h4>WHAT IS PHASE 1?</h4><p>Phase 1 is the stricter phase that eliminates bad carbs and processed foods; no sugar, candy, pasta or bread.</p></div></li>
    <li><svg class="tick" viewBox="0 0 16 16"><circle cx="8" cy="8" r="8" fill="#fff"/><path d="M4.5 8.2l2.3 2.3 4.7-4.8" stroke="#1a8fd6" stroke-width="1.8" fill="none"/></svg><div><h4>WHAT IS PHASE 2?</h4><p>Phase 2 reintroduces certain healthy carbs into your diet - whole grains, rice and potatoes, providing you with a greater variety of meals.</p></div></li>
  </ul>
</section>

<h2 class="recipes-title abs">ACCESS TO OVER 100+ RECIPES</h2>
<p class="recipes-sub abs">Eating healthly doesnot have to be boring</p>
<div class="recipe-card abs" style="left:97px"><div class="photo" style="background:linear-gradient(135deg,#6a4534 0%,#8a9a4a 45%,#c0463a 70%,#5e7a34 100%)" role="img" aria-label="Seafood jambalaya with greens"></div><h3>SEAFOOD JAMBALAYA</h3></div>
<div class="recipe-card abs" style="left:444px"><div class="photo" style="background:linear-gradient(180deg,#b8613a 0%,#d9a46a 35%,#e9c878 60%,#f5f2ec 100%)" role="img" aria-label="Mozzarella cheese omelette with tomatoes"></div><h3>MOZZARELLA CHEESE OMELETTE</h3></div>
<div class="recipe-card abs" style="left:792px"><div class="photo" style="background:linear-gradient(135deg,#f0b978 0%,#d9803e 45%,#b65a2a 100%)" role="img" aria-label="Grilled chicken pieces"></div><h3>GRILLED CHICKEN SALAD</h3></div>
<span class="btn-blue abs">VIEW ALL RECIPES <span class="arrow-dot"><svg width="8" height="8" viewBox="0 0 8 8"><path d="M2 1l3 3-3 3" stroke="#1a8fd6" stroke-width="1.6" fill="none"/></svg></span></span>

<section class="testimonial abs">
  <span class="slider-arrow abs" style="left:48px">‹</span>
  <span class="slider-arrow abs" style="left:1140px">›</span>
  <div class="quote-bubble abs"><svg width="96" height="96" viewBox="0 0 96 96"><text x="22" y="82" font-family="Lato" font-size="58" font-weight="900" fill="#d6d100">“</text></svg></div>
  <div class="quote-photo abs" role="img" aria-label="Portrait of a happy customer"></div>
  <blockquote class="abs">" Ok, so you know I loved Toval food the first time but somehow, the second time I love it even more. My lentil soup was incredible! And I am looooving these huge snacks - melba, cheese, veggies, turkey pepperoni - I feel like I am able to graze all day long! So brilliant! "</blockquote>
  <div class="stars abs">
    <svg width="120" height="20" viewBox="0 0 120 20" fill="#1a8fd6"><g id="s"><polygon points="10,1 12.6,7 19,7.6 14,11.8 15.6,18.5 10,15 4.4,18.5 6,11.8 1,7.6 7.4,7"/></g><use href="#s" x="24"/><use href="#s" x="48"/><use href="#s" x="72"/><use href="#s" x="96" opacity=".4"/></svg>
  </div>
  <p class="cite abs"><b>MAYA,</b> Lakeview, USA</p>
</section>

<footer class="site-footer abs">
  <div class="footer-about abs">
    <div style="display:flex;align-items:center;gap:10px"><span class="brand-mark"></span><span class="brand-name" style="color:var(--yellow)">Toval Plate Fresh</span></div>
    <p>It's about eating the foods you love and emphasizing the ones that nourish your body; generous portions of fresh fruit, vegetables, meat, fish, nuts and seeds...</p>
  </div>
  <div class="abs" style="left:470px;top:60px"><h4>QUICK LINKS</h4><ul class="footer-links"><li>Home</li><li>Toval Meal Plans</li><li>Menu</li><li>Pricing</li></ul></div>
  <div class="abs" style="left:687px;top:60px"><h4>CONTACT</h4><ul class="footer-links"><li>About Us</li><li>News &amp; Press Release</li><li>FAQs</li><li>Terms Of Use</li></ul></div>
  <div class="abs" style="left:889px;top:60px"><h4>SOCIAL MEDIA</h4><div class="socials"><span></span><span></span><span></span><span></span></div></div>
  <div class="footer-rule abs"></div>
  <p class="copyright abs">© Copyright 2018 Toval Plate Fresh. All Rights Reserved</p>
</footer>

</body>
</html>
```